PDF flyer for our companies' two main products: Food processing machines.

PDF flyer with showcasing two products. Flyer can be one page per product, or both products on the same page.

Product #1: Labeled "Ribbon blenders".
Showing a photo of the machine, and the details/features offered with that machine. Product description must also say: "Sizes available; 2 Cu Ft. - 450 Cu Ft."

Product #2: Labeled: " Auger hoppers / Screw feeders"
Showing a photo of the machine, and the details/features offered with that machine.

SEE UPLOADED IMAGES; "Ribbon Blenders EXAMPLE FLYER".
& "Auger Hoppers / Screw Conveyors EXAMPLE FLYER" for a rough idea of what we are looking for.

Target Market(s)

Copackers, Packing houses, Food manufacturers, protein powder producers,

Industry/Entity Type

Commercial Food processing / packing / mixing equipment

Font styles to use
Serif

Colors
0054AA
0677BA
7BADD7
CADEEF
E8F1F8

Requirements
Must have
• Company logo on top of flyer.
Nice to have
• I would like for the flyer to show some stock images of common ingredients, similar to the images uploaded.
Should not have
• Pictures with background. Backgrounds must be removed from provides photos. "clipping path"

```html
<!DOCTYPE html>
<html lang="en">
<head>
<meta charset="utf-8">
<title>Keystone Equipment – Product Flyers</title>
<link href="https://fonts.googleapis.com/css2?family=Roboto:wght@400;500;700&display=swap" rel="stylesheet">
<style>
:root{
  --blue:#0054AA;
  --blue-mid:#0677BA;
  --blue-soft:#7BADD7;
  --blue-pale:#CADEEF;
  --blue-mist:#E8F1F8;
  --ink:#111;
  --black:#0a0a0a;
  --white:#fff;
}
*{box-sizing:border-box;margin:0;padding:0}
html,body{width:1200px;height:856px;overflow:hidden}
body{background:var(--blue-mist);font-family:'Roboto',Arial,sans-serif;color:var(--ink);position:relative}
.page{position:absolute;top:80px;width:488px;height:691px;background:#fff;overflow:hidden;box-shadow:0 3px 10px rgba(0,40,90,.18)}
.page--auger{left:91px}
.page--ribbon{left:625px}
.page-bg{position:absolute;inset:0;width:100%;height:100%}
.brand{position:absolute;left:5px;top:13px;width:168px;height:47px;border-radius:50%;background:var(--black);border:2px solid var(--blue-mid);display:flex;align-items:center;justify-content:center;gap:6px;color:#fff;font-weight:700;font-size:14px;letter-spacing:1px}
.brand-dot{width:8px;height:8px;border-radius:50%;background:#fff}
.product-photo{position:absolute;border-radius:6px;background:linear-gradient(150deg,#e3e6ea,#9aa1a9 60%,#6d747c)}
.product-title{position:absolute;color:var(--blue);font-weight:700;line-height:1.08;white-space:nowrap}
.rule{position:absolute;height:1.5px;background:#1a2a44}
.sizes{position:absolute;font-size:11.5px;line-height:1.4;color:#111;font-weight:500}
.section-head{position:absolute;color:var(--blue);font-size:12px;font-weight:500}
.features{position:absolute;list-style:none;font-size:6.6px;color:#111}
.features li{position:relative;padding-left:9px}
.features li::before{content:"";position:absolute;left:0;top:2.3px;width:3px;height:3px;border-radius:50%;background:var(--blue)}
.features li.sub::before{display:none}
.options-head{position:absolute;color:#fff;font-size:12px;font-weight:400}
.options{position:absolute;list-style:none;font-size:6.6px;color:#fff}
.options li{position:relative;padding-left:9px}
.options li::before{content:"";position:absolute;left:0;top:2.3px;width:3px;height:3px;border-radius:50%;background:#fff}
.ingredient{position:absolute;border-radius:50%;border:3px solid #fff;box-shadow:0 1px 4px rgba(0,0,0,.25)}
.spice-main{background:radial-gradient(circle,#b07a3f 0%,#c99560 45%,#f4f1ee 75%)}
.spice-ginger{background:radial-gradient(circle,#d9b27a 0%,#f2ece4 70%)}
.spice-nut{background:radial-gradient(circle,#5a3b2a 0%,#a48874 45%,#f0ece8 75%)}
.spice-cinnamon{background:radial-gradient(circle,#9a5430 0%,#d7a27f 45%,#f4efea 75%)}
.spice-cardamom{background:radial-gradient(circle,#8f8a4f 0%,#cfcaa0 45%,#f5f3ea 75%)}
.spec-table{position:absolute;border-collapse:collapse;background:#fff}
.spec-table--auger{left:29px;top:545px;width:430px;font-size:8.3px}
.spec-table--auger td{border:1.4px solid #111;padding:0 2px;height:13px;line-height:12px;white-space:nowrap}
.spec-table--auger td.c{text-align:center}
.spec-table--ribbon{left:74px;top:534px;width:343px;font-size:4.3px;box-shadow:0 1px 3px rgba(0,0,0,.2)}
.spec-table--ribbon td{border:.5px solid #999;padding:0 1px;height:7.8px;line-height:7px;white-space:nowrap}
.spec-table--ribbon tr:first-child td{font-weight:700}
.footer{position:absolute;left:0;right:0;bottom:0;height:16px;background:var(--black);color:#fff;font-size:6.8px;display:flex;align-items:center;justify-content:center;gap:38px}
.footer span{display:flex;align-items:center;gap:5px}
.footer svg{width:7px;height:7px;fill:#fff}
</style>
</head>
<body>

<section class="page page--auger">
  <svg class="page-bg" viewBox="0 0 488 691" preserveAspectRatio="none" aria-hidden="true">
    <defs>
      <linearGradient id="fadeA" x1="0" y1="0" x2="0" y2="1"><stop offset="0" stop-color="#f6f8fb"/><stop offset="1" stop-color="#e9eef4"/></linearGradient>
    </defs>
    <rect width="488" height="691" fill="url(#fadeA)"/>
    <polygon points="0,0 430,0 0,150" fill="var(--blue)"/>
    <polygon points="0,180 330,100 0,240" fill="var(--blue)" opacity=".9"/>
    <polygon points="330,0 488,0 488,55" fill="var(--black)"/>
    <polygon points="0,362 488,362 488,510 0,520" fill="var(--blue)"/>
    <polygon points="0,362 488,362 488,440 0,470" fill="var(--blue-mid)" opacity=".35"/>
  </svg>
  <div class="brand"><span class="brand-dot"></span>KEYSTONE</div>
  <div class="product-photo" role="img" aria-label="Stainless steel auger hopper with inclined screw conveyor on castor wheels" style="left:22px;top:58px;width:300px;height:276px;clip-path:polygon(0 72%,78% 0,100% 4%,40% 100%,0 100%)"></div>
  <h1 class="product-title" style="left:297px;top:137px;font-size:19.5px">AUGER HOPPERS /<br>SCREW CONVEYORS</h1>
  <div class="rule" style="left:297px;top:188px;width:74px"></div>
  <h2 class="section-head" style="left:297px;top:210px">Standard Features:</h2>
  <ul class="features" style="left:297px;top:232px;line-height:15.8px">
    <li>Direct Drive</li>
    <li>-304 Stainless steel construction.</li>
    <li>Stainless steel safety grating.</li>
    <li>Pre-wired control panel</li>
    <li>Electric Vibrator</li>
    <li>Castor Wheels.</li>
  </ul>
  <h2 class="options-head" style="left:6px;top:395px">Options:</h2>
  <ul class="options" style="left:6px;top:418px;line-height:15.8px">
    <li>Square or round hopper. 3.5cf and 7cf hoppers are standard.</li>
    <li>Custom hoppers up to 200cf.</li>
    <li>VFD (Variable Frequency Drive).</li>
    <li>Clamshell Auger tube for easy cleanout.</li>
    <li>316 Stainless steel construction.</li>
  </ul>
  <div class="ingredient spice-main" role="img" aria-label="Pile of ground spice" style="left:325px;top:346px;width:152px;height:152px"></div>
  <div class="ingredient spice-ginger" role="img" aria-label="Ginger root" style="left:276px;top:385px;width:54px;height:54px"></div>
  <div class="ingredient spice-nut" role="img" aria-label="Whole nutmeg" style="left:288px;top:433px;width:54px;height:54px"></div>
  <div class="ingredient spice-cinnamon" role="img" aria-label="Cinnamon sticks" style="left:326px;top:463px;width:54px;height:54px"></div>
  <div class="ingredient spice-cardamom" role="img" aria-label="Green cardamom pods" style="left:376px;top:472px;width:54px;height:54px"></div>
  <table class="spec-table spec-table--auger">
    <tr><td>MODEL</td><td>AH-A2</td><td>AH-A3</td><td>AH-A5</td><td>AH-A7</td><td>AH-A8</td><td>AH-A12</td></tr>
    <tr><td>FEEDING RATE</td><td>2m³/Hr</td><td>3m³/Hr</td><td>5m³/Hr</td><td>7m³/Hr</td><td>8m³/Hr</td><td>12m³/Hr</td></tr>
    <tr><td>PIPE DIAMETER</td><td>4"</td><td>4-1/2"</td><td>5-1/2"</td><td>6-1/4"</td><td>6-1/2"</td><td>8-1/2"</td></tr>
    <tr><td>HOPPER VOL.</td><td>3.5CF</td><td class="c" colspan="5">7CF</td></tr>
    <tr><td>DIMENSIONS</td><td>28.6"x24.4"x31.5"</td><td class="c" colspan="5">40" x 32" x 35"</td></tr>
    <tr><td>TOTAL WEIGHT</td><td>221LBS</td><td>287LBS</td><td>397LBS</td><td>441LBS</td><td>485LBS</td><td>596LBS</td></tr>
    <tr><td>CHARGING HEIGHT</td><td class="c" colspan="6">STANDARD 72 INCHES. (40" - 196" AVAILABLE)</td></tr>
    <tr><td>CHARGING ANGLE</td><td class="c" colspan="6">STANDARD 45°&nbsp;&nbsp;&nbsp;&nbsp;(30°-60° AVAILABLE)</td></tr>
  </table>
  <footer class="footer">
    <span><svg viewBox="0 0 24 24"><path d="M6.6 10.8a15 15 0 0 0 6.6 6.6l2.2-2.2c.3-.3.7-.4 1-.2 1.1.4 2.3.6 3.6.6.6 0 1 .4 1 1V20c0 .6-.4 1-1 1A17 17 0 0 1 3 4c0-.6.4-1 1-1h3.5c.6 0 1 .4 1 1 0 1.3.2 2.5.6 3.6.1.3 0 .7-.2 1z"/></svg>+1 800-555-0142</span>
    <span><svg viewBox="0 0 24 24"><path d="M2 5h20v14H2zM4 7v.5l8 5 8-5V7l-8 5z"/></svg>info@keystone-equip.com</span>
  </footer>
</section>

<section class="page page--ribbon">
  <svg class="page-bg" viewBox="0 0 488 691" preserveAspectRatio="none" aria-hidden="true">
    <defs>
      <linearGradient id="fadeB" x1="0" y1="0" x2="0" y2="1"><stop offset="0" stop-color="#f6f8fb"/><stop offset="1" stop-color="#e9eef4"/></linearGradient>
    </defs>
    <rect width="488" height="691" fill="url(#fadeB)"/>
    <polygon points="0,0 430,0 0,150" fill="var(--blue)"/>
    <polygon points="0,180 330,100 0,240" fill="var(--blue)" opacity=".9"/>
    <polygon points="330,0 488,0 488,55" fill="var(--black)"/>
    <polygon points="0,362 488,362 488,510 0,520" fill="var(--blue)"/>
    <polygon points="0,362 488,362 488,440 0,470" fill="var(--blue-mid)" opacity=".35"/>
  </svg>
  <div class="brand"><span class="brand-dot"></span>KEYSTONE</div>
  <div class="product-photo" role="img" aria-label="Stainless steel ribbon blender with control panel on a wheeled frame" style="left:10px;top:88px;width:245px;height:260px"></div>
  <h1 class="product-title" style="left:288px;top:66px;font-size:19.5px">RIBBON BLENDERS</h1>
  <div class="rule" style="left:288px;top:91px;width:74px"></div>
  <p class="sizes" style="left:288px;top:100px">SIZES OFFERED:<br>2 Cu Ft - 450 Cu Ft</p>
  <h2 class="section-head" style="left:288px;top:139px">Standard Features:</h2>
  <ul class="features" style="left:288px;top:160px;line-height:12.8px">
    <li>304 stainless steel construction.</li>
    <li>Pre-wired control panels with;</li>
    <li class="sub">- Batch timer,</li>
    <li class="sub">- On/Off switch,</li>
    <li class="sub">- Emergency stop button.</li>
    <li style="margin-top:3px">Food grade compression shaft seals.</li>
    <li style="margin-top:3px">Safety sensor on lid for automatic shutoff when opened.</li>
    <li style="margin-top:3px">Air actuated discharge valve.</li>
    <li style="margin-top:3px">1 piece hinged lid with safety grating.</li>
    <li style="margin-top:3px">Power options; 220v/4.80v.</li>
    <li style="margin-top:3px">24' standard discharge height.</li>
    <li style="margin-top:3px">Castor wheels on 53cf units and smaller</li>
  </ul>
  <h2 class="options-head" style="left:6px;top:387px">Options:</h2>
  <ul class="options" style="left:6px;top:408px;line-height:15.8px">
    <li>Dual hinged lids available on custom orders.</li>
    <li>Knife gate style discharge available on custom orders.</li>
    <li>Air purge seals available on custom orders.</li>
    <li>316 stainless material available on custom orders.</li>
  </ul>
  <ul class="options" style="left:186px;top:408px;line-height:15.8px">
    <li>Custom height modification.</li>
    <li>Liquid spray systems</li>
    <li>(VFD) Variable Frequency Drives</li>
    <li>Leg extensions</li>
  </ul>
  <div class="ingredient spice-main" role="img" aria-label="Pile of ground spice" style="left:355px;top:365px;width:130px;height:130px"></div>
  <div class="ingredient spice-ginger" role="img" aria-label="Ginger root" style="left:314px;top:402px;width:48px;height:48px"></div>
  <div class="ingredient spice-nut" role="img" aria-label="Whole nutmeg" style="left:324px;top:445px;width:48px;height:48px"></div>
  <div class="ingredient spice-cinnamon" role="img" aria-label="Cinnamon sticks" style="left:360px;top:471px;width:48px;height:48px"></div>
  <div class="ingredient spice-cardamom" role="img" aria-label="Green cardamom pods" style="left:405px;top:482px;width:48px;height:48px"></div>
  <table class="spec-table spec-table--ribbon">
    <tr><td>Model Size</td><td>5cf</td><td>7CF</td><td>10.5CF</td><td>17.5CF</td><td>35CF</td><td>53CF</td><td>70.5CF</td><td>106CF</td></tr>
    <tr><td>Working Liters</td><td>120L</td><td>200L</td><td>300L</td><td>500L</td><td>1000L</td><td>1500L</td><td>2000L</td><td>3000L</td></tr>
    <tr><td>Fill Capicty</td><td>5CF / 150L</td><td>9CF / 250L</td><td>13CF / 375L</td><td>22CF / 625L</td><td>44CF / 1250L</td><td>66CF / 1875L</td><td>88CF / 2500L</td><td>132CF / 3750L</td></tr>
    <tr><td>Weight</td><td>440lbs</td><td>550lbs</td><td>770lbs</td><td>1212lbs</td><td>1874lbs</td><td>2645lbs</td><td>3527lbs</td><td>5511lbs</td></tr>
    <tr><td>Motor Size</td><td>4hp</td><td>5.3hp</td><td>6.7hp</td><td>10hp</td><td>14.75hp</td><td>20hp</td><td>25hp</td><td>30hp</td></tr>
    <tr><td>Total Length</td><td>50"</td><td>53.5"</td><td>63"</td><td>72"</td><td>94"</td><td>102"</td><td>131.5"</td><td>157.5"</td></tr>
    <tr><td>Total Width</td><td>28"</td><td>34"</td><td>41.5"</td><td>45"</td><td>52"</td><td>66"</td><td>52.5"</td><td>54"</td></tr>
    <tr><td>Total Height</td><td>66"</td><td>69"</td><td>71"</td><td>82"</td><td>87"</td><td>95"</td><td>76"</td><td>110"</td></tr>
    <tr><td>Tub Length</td><td>31.5"</td><td>35.5"</td><td>41"</td><td>47"</td><td>59"</td><td>70"</td><td>75"</td><td>100"</td></tr>
    <tr><td>Tub Width</td><td>16.5"</td><td>22"</td><td>25"</td><td>27.5"</td><td>35.5"</td><td>39"</td><td>48"</td><td>48"</td></tr>
    <tr><td>Tub Height</td><td>20.5"</td><td>26"</td><td>28"</td><td>33"</td><td>41"</td><td>46"</td><td>51"</td><td>53"</td></tr>
    <tr><td>Shaft Diameter</td><td>2"</td><td>2-1/4"</td><td>2-5/8"</td><td>3"</td><td>3.5"</td><td>4"</td><td>4"</td><td>5-1/4"</td></tr>
    <tr><td>Tub Thickness</td><td>3mm</td><td>3mm</td><td>3mm</td><td>4mm</td><td>4mm</td><td>5mm</td><td>5mm</td><td>6mm</td></tr>
    <tr><td>Ribbon Thickness</td><td>6mm</td><td>8mm</td><td>8mm</td><td>8mm</td><td>10mm</td><td>12mm</td><td>12mm</td><td>14mm</td></tr>
    <tr><td>Max RPM</td><td>46 rpm</td><td>46 rpm</td><td>46 rpm</td><td>46 rpm</td><td>30 rpm</td><td>31 rpm</td><td>32 rpm</td><td>33 rpm</td></tr>
  </table>
  <footer class="footer">
    <span><svg viewBox="0 0 24 24"><path d="M6.6 10.8a15 15 0 0 0 6.6 6.6l2.2-2.2c.3-.3.7-.4 1-.2 1.1.4 2.3.6 3.6.6.6 0 1 .4 1 1V20c0 .6-.4 1-1 1A17 17 0 0 1 3 4c0-.6.4-1 1-1h3.5c.6 0 1 .4 1 1 0 1.3.2 2.5.6 3.6.1.3 0 .7-.2 1z"/></svg>+1 800-555-0142</span>
    <span><svg viewBox="0 0 24 24"><path d="M2 5h20v14H2zM4 7v.5l8 5 8-5V7l-8 5z"/></svg>info@keystone-equip.com</span>
  </footer>
</section>

</body>
</html>
```